Fitness Centre/Personal Trainer Business Card

We need a business card design for a company based in Singapore called 'Vigor Ledger'.

We are a team of Personal Trainers and we are planning to open our new training facility.

This design will also be printed/painted on the walls in our gym.

We are a new breed of personal trainers who take fitness seriously and holistically. We do not merely train our clients to be big and muscular.

We believe in wholeness. In our opinion, fitness should include: strength, speed, flexibility, mobility, stamina & agility. These are what we train for. Of course, nutrition/diet is key.

We use fitness tools such as kettlebells, QVL, Pylometric boxes, battling ropes, clubbells, medicine balls, bulgarian bags etc - functional and non-bulky tools.

I currently have a Facebook page 'Vigor Ledger SG' which shows a logo of a kettlebell. But my business focus has since changed.

Services provided:
- Kettlebell Sport Preparation
- Calisthenics Training
- Corrective Exercises
- Sports Strength & Conditioning
- 28 days Weight Loss Program
- Myofascial Rehab Therapy
- Sports/Thai Massage

Main colors for the design should be BLACK & YELLOW. We envision a design which is able to protray the holistic view we take on fitness. Also it should somewhat appeal to the ladies and not intimidate them.

Target Market(s)

People between 18-35 years old. Students and working class alike.

Industry/Entity Type

Training

Requirements
Must have
• Name: Marcus Obadiah Lim
Fitness Coach
Corrective Exercise Specialist
M: +65 9437 2065
E: marcus@sgvigorledger-example.com

Double-sided please.
Nice to have
• "What is your vigor ledger?"

```html
<!DOCTYPE html>
<html lang="en">
<head>
<meta charset="utf-8">
<title>Vigor Ledger – Business Card</title>
<link href="https://fonts.googleapis.com/css2?family=Open+Sans:wght@400;600;700&display=swap" rel="stylesheet">
<style>
  :root{
    --backdrop:#e4e2de;
    --card-black:#050505;
    --card-charcoal:#2a2a2a;
    --card-charcoal-deep:#1b1b1b;
    --band-grey:#5a5a5a;
    --brand-yellow:#f5d313;
    --text-white:#f2f2f2;
    --divider:#777;
  }
  *{margin:0;padding:0;box-sizing:border-box}
  html,body{width:1200px;height:722px;overflow:hidden}
  body{background:var(--backdrop);font-family:"Open Sans",Arial,sans-serif;position:relative}

  .card{position:absolute;width:515px;height:294px;overflow:hidden;box-shadow:0 4px 10px rgba(0,0,0,.35)}
  .card--front{left:404px;top:51px;background:linear-gradient(180deg,var(--card-charcoal) 0%,var(--card-charcoal-deep) 100%)}
  .card--services-list{left:91px;top:375px;background:var(--card-black)}
  .card--services-grid{left:635px;top:382px;background:var(--card-black)}

  .brand-mark{position:absolute;display:flex;align-items:center;gap:10px;color:var(--brand-yellow);font-weight:700;line-height:1.05}
  .brand-mark__dot{width:14px;height:14px;border-radius:50%;background:var(--brand-yellow);flex:none}
  .card--front .brand-mark{left:66px;top:100px;font-size:27px}
  .card--services-list .brand-mark{left:52px;top:100px;font-size:28px}

  .front__divider{position:absolute;left:262px;top:55px;width:2px;height:110px;background:linear-gradient(180deg,transparent,var(--divider),transparent)}
  .front__details{position:absolute;left:285px;top:78px;color:var(--text-white);font-size:13px;line-height:19px}
  .front__name{color:var(--brand-yellow);font-weight:700;font-size:17px;line-height:24px}
  .front__contacts{margin-top:14px;list-style:none}
  .front__contacts li{display:flex;align-items:center;gap:6px}
  .front__contacts svg{flex:none}

  .front__band{position:absolute;left:0;top:0}
  .tagline{position:absolute;left:0;width:100%;text-align:center;color:var(--brand-yellow);font-weight:700;font-size:16px;letter-spacing:1.3px}
  .card--front .tagline{top:268px}
  .card--services-list .tagline{top:270px}
  .card--services-grid .tagline{top:254px}

  .services__title{position:absolute;color:var(--brand-yellow);font-weight:700;font-size:18px}
  .card--services-list .services__title{left:270px;top:26px}
  .services__list{position:absolute;left:268px;top:67px;list-style:none;color:var(--text-white);font-size:15px;line-height:26.5px}
  .services__list li::before{content:"";display:inline-block;width:5px;height:5px;border-radius:50%;background:var(--text-white);margin:0 5px 3px 0}

  .services-grid__watermark{position:absolute;left:0;top:112px;width:100%;text-align:center;color:var(--brand-yellow);opacity:.18;font-weight:700;font-size:46px}
  .card--services-grid .services__title{left:0;width:100%;text-align:center;top:70px}
  .services-grid__rows{position:absolute;left:0;top:118px;width:100%;text-align:center;color:var(--brand-yellow);font-size:17px;line-height:33px;letter-spacing:.2px}
  .services-grid__rows span::before{content:"";display:inline-block;width:6px;height:6px;border-radius:50%;background:var(--brand-yellow);margin:0 5px 4px 8px}
</style>
</head>
<body>

<section class="card card--front" aria-label="Business card front">
  <div class="brand-mark"><span class="brand-mark__dot"></span><span>Vigor<br>Ledger</span></div>
  <div class="front__divider"></div>
  <div class="front__details">
    <p class="front__name">Marcus Obadiah Lim</p>
    <p>Fitness Coach</p>
    <p>Corrective Exercise Specialist</p>
    <ul class="front__contacts">
      <li><svg width="8" height="11" viewBox="0 0 8 11"><rect x="1" y="0.5" width="6" height="10" rx="1" fill="none" stroke="#f5d313"/><rect x="2.5" y="2" width="3" height="5" fill="#f5d313"/></svg>+65 9437 2065</li>
      <li><svg width="9" height="7" viewBox="0 0 9 7"><rect width="9" height="7" fill="#f5d313"/><path d="M0 0l4.5 3.5L9 0" stroke="#2a2a2a" fill="none"/></svg>marcus@sgvigorledger-example.com</li>
      <li><svg width="9" height="9" viewBox="0 0 9 9"><circle cx="4.5" cy="4.5" r="4" fill="none" stroke="#f5d313"/><path d="M0.5 4.5h8M4.5 0.5v8" stroke="#f5d313"/></svg>www.sgvigorledger-example.com</li>
    </ul>
  </div>
  <svg class="front__band" width="515" height="294" viewBox="0 0 515 294">
    <path d="M0 252 Q220 226 515 280 L515 294 L0 294 Z" fill="var(--brand-yellow)"/>
    <path d="M0 258 Q220 236 515 290 L515 294 L0 294 Z" fill="var(--band-grey)"/>
  </svg>
  <p class="tagline">WHAT IS YOUR VIGOR LEDGER ?</p>
</section>

<section class="card card--services-list" aria-label="Business card back, services list">
  <div class="brand-mark"><span class="brand-mark__dot"></span><span>Vigor<br>Ledger</span></div>
  <h2 class="services__title">Services</h2>
  <ul class="services__list">
    <li>Sports Strength &amp; Conditioning</li>
    <li>Kettlebell Sport Preparation</li>
    <li>28 days Weight Loss Program</li>
    <li>Myofascial Rehab Therapy</li>
    <li>Calisthenics Training</li>
    <li>Corrective Exercises</li>
    <li>Sports/Thai Massage</li>
  </ul>
  <p class="tagline">WHAT IS YOUR VIGOR LEDGER ?</p>
</section>

<section class="card card--services-grid" aria-label="Business card back, services overview">
  <p class="services-grid__watermark" aria-hidden="true">Vigor Ledger</p>
  <h2 class="services__title">Services</h2>
  <div class="services-grid__rows">
    <p><span>Sports Strength &amp; Conditioning</span> <span>Sports/Thai Massage</span></p>
    <p><span>Kettlebell Sport Preparation</span> <span>Corrective Exercises</span></p>
    <p><span>28 days Weight Loss Program</span> <span>Calisthenics Training</span></p>
    <p><span>Myofascial Rehab Therapy</span></p>
  </div>
  <p class="tagline">WHAT IS YOUR VIGOR LEDGER ?</p>
</section>

</body>
</html>
```